Create a memorable Web Design for real estate branding

we are a Minnepolis brokerage and boutique housing specialist with over 27 years of experience in the Global furnished housing industry, servicing the Greater Los Angeles area. Specializing in “warm environments” we offer a customized approach to satisfying our guests and client’s needs by offering a wide array of options in highly desirable areas. Additionally, Lantern Dwelling Partners offers assistance and expertise to home buyers, sellers and investors.

Industry/Entity Type

Real Estate

Number of Pages Required

1 page

Font styles to use
Serif
Sans Serif
Decorative

```html
<!DOCTYPE html>
<html lang="en">
<head>
<meta charset="utf-8">
<title>Lantern Dwelling Partners – Real Estate</title>
<link href="https://fonts.googleapis.com/css2?family=Ubuntu:wght@300;400;500;700&display=swap" rel="stylesheet">
<style>
:root{
  --black:#000;
  --ink:#222;
  --muted:#555;
  --green:#8dc63f;
  --green-dark:#6e9d2c;
  --lime:#b8d44a;
  --teal:#17a58a;
  --teal-dark:#128a73;
  --band:#e5e5e5;
  --card:#f5f5f5;
  --white:#fff;
  --footer-bottom:#0d0d0d;
}
*{box-sizing:border-box;margin:0;padding:0}
html,body{width:1200px;height:2473px;overflow:hidden}
body{position:relative;font-family:"Ubuntu",sans-serif;color:var(--ink);background:var(--white)}
.abs{position:absolute}

/* header */
.site-header{position:absolute;left:0;top:0;width:1200px;height:109px;background:var(--black)}
.brand{position:absolute;left:132px;top:30px;color:var(--teal);font-weight:500;font-size:22px;line-height:25px;letter-spacing:.5px}
.main-nav a{position:absolute;top:44px;font-size:14px;color:var(--lime);text-decoration:none}
.main-nav .active::after{content:"";position:absolute;left:-10px;right:-10px;top:62px;height:3px;background:var(--teal)}
.search-toggle{position:absolute;left:1004px;top:37px;width:36px;height:36px;background:var(--teal);display:flex;align-items:center;justify-content:center}

/* hero */
.hero{position:absolute;left:0;top:109px;width:1200px;height:481px;background:linear-gradient(180deg,#2f6db8 0%,#5c94d6 35%,#8a8c8a 60%,#5e7a3c 85%,#8caa48 100%)}
.hero-title{position:absolute;left:0;width:1200px;top:193px;text-align:center;color:var(--white);font-size:30px;font-weight:500;text-shadow:0 2px 4px rgba(0,0,0,.5)}
.slider-dots{position:absolute;top:385px;left:548px;display:flex;gap:10px}
.slider-dots span{width:30px;height:4px;background:rgba(255,255,255,.85)}

/* property search */
.finder-shadow{position:absolute;left:200px;top:640px;width:800px;height:24px;border-radius:50%;box-shadow:0 14px 18px rgba(0,0,0,.35)}
.finder{position:absolute;left:132px;top:517px;width:936px;height:134px}
.finder h2{position:absolute;left:39px;top:23px;color:var(--white);font-weight:400;font-size:19px}
.field{position:absolute;top:63px}
.field label{display:block;color:var(--white);font-size:11px;margin-bottom:5px}
.field .box{height:28px;background:var(--white);border:1px solid #cfcfcf;font-size:10px;color:#999;padding:8px 6px;position:relative}
.field .box.select::after{content:"";position:absolute;right:7px;top:11px;border:4px solid transparent;border-top:5px solid #333}
.field .box.select::before{content:"";position:absolute;right:22px;top:3px;bottom:3px;width:1px;background:#ccc}
.finder .search-btn{position:absolute;left:807px;top:76px;width:104px;height:28px;background:var(--teal);color:var(--white);font-size:14px;text-align:center;line-height:28px}

/* intro */
.section-title{position:absolute;left:0;width:1200px;text-align:center;color:var(--teal);font-weight:400}
.intro-title{top:692px;font-size:27px}
.intro-text{position:absolute;left:206px;width:791px;top:736px;text-align:center;font-size:11.5px;line-height:20px;color:var(--muted)}
.btn-teal{position:absolute;background:var(--teal);color:var(--white);text-align:center;font-size:12px}
.intro-btn{left:549px;top:812px;width:102px;height:30px;line-height:30px}

/* tabs */
.tabs a{position:absolute;top:880px;font-size:14px;font-weight:500;color:#333;text-decoration:none}
.tabs .active::after{content:"";position:absolute;left:-6px;right:-6px;top:24px;height:2px;background:var(--teal)}

/* listing cards */
.listing{position:absolute;width:285px;height:322px;background:var(--card);box-shadow:0 6px 10px rgba(0,0,0,.14)}
.listing .photo{position:absolute;left:0;top:0;width:285px;height:209px}
.listing .tag{position:absolute;left:193px;top:14px;width:99px;height:31px;background:var(--green);color:var(--white);font-size:12px;text-align:center;line-height:31px}
.listing .tag::after{content:"";position:absolute;right:0;bottom:-7px;border-left:7px solid var(--green-dark);border-bottom:7px solid transparent}
.listing .address{position:absolute;left:0;top:222px;width:285px;text-align:center;font-size:13.5px;line-height:18px;font-weight:500;color:#333}
.listing .rule{position:absolute;left:8px;right:8px;top:271px;border-top:1px dashed #aaa}
.listing .price{position:absolute;left:22px;top:286px;font-size:10.5px;color:#333}
.listing .our{position:absolute;right:20px;top:286px;font-size:10.5px;color:#333}
.listing.open{background:#262630}
.listing.open .details{position:absolute;left:32px;top:60px;width:230px;color:var(--white);font-size:10.5px;line-height:16px}
.details .spec{color:var(--lime);font-size:12px;line-height:20px}
.details p{margin-top:12px}
.details .date{color:var(--lime);margin-top:8px}
.details .view{position:absolute;left:141px;top:102px;width:84px;height:24px;border:1px solid #ddd;text-align:center;line-height:22px;font-size:10.5px;color:var(--white)}
.listing.open .address{color:var(--lime)}
.listing.open .price,.listing.open .our{color:var(--lime)}

/* testimonials */
.testi-title{top:1643px;font-size:33px}
.testimonial{position:absolute;top:1717px;width:300px;height:318px;background:var(--white);box-shadow:0 4px 10px rgba(0,0,0,.16)}
.testimonial .head{position:absolute;left:0;top:0;width:100%;height:112px;background:#e3e3e3}
.testimonial h3{position:absolute;left:0;width:100%;top:20px;text-align:center;font-size:16px;font-weight:400;color:#111}
.testimonial .avatar{position:absolute;left:104px;top:50px;width:92px;height:92px;border-radius:50%;border:3px solid var(--white)}
.testimonial blockquote{position:absolute;left:28px;width:244px;top:165px;text-align:center;font-size:11.5px;line-height:20px;color:#333}
.testimonial .btn-teal{left:112px;top:256px;width:76px;height:23px;line-height:23px;font-size:11px}

/* newsletter */
.join{position:absolute;left:0;top:2072px;width:1200px;height:145px;background:var(--band)}
.join h2{position:absolute;right:722px;top:38px;font-size:40px;font-weight:400;color:#111;letter-spacing:1px}
.join .sub{position:absolute;right:722px;top:86px;font-size:12.5px;color:#222}
.join .email{position:absolute;left:499px;top:57px;width:297px;height:37px;background:var(--white);font-size:10px;color:#666;padding:13px 16px}
.join .email svg{position:absolute;right:16px;top:13px}
.join .btn-teal{left:809px;top:57px;width:120px;height:37px;line-height:37px;font-size:15px}

/* footer */
.site-footer{position:absolute;left:0;top:2217px;width:1200px;height:201px;background:var(--black)}
.site-footer h4{position:absolute;top:34px;color:var(--teal);font-size:15px;font-weight:400}
.quick-links{position:absolute;left:193px;top:62px;list-style:none}
.quick-links li{color:var(--teal);font-size:12px;line-height:24px}
.quick-links li::before{content:"›";display:inline-block;width:20px;color:#ccc}
.contact-line{position:absolute;left:541px;color:var(--teal);font-size:12px;line-height:18px}
.contact-icon{position:absolute;left:514px}
.socials{position:absolute;left:809px;top:2281px;display:flex;gap:7px}
.socials span{width:26px;height:26px;border-radius:50%;border:1px solid #bbb}
.footer-brand{position:absolute;left:809px;top:2344px;color:var(--teal);font-size:18px;font-weight:500;line-height:20px}
.copyright{position:absolute;left:0;top:2418px;width:1200px;height:55px;background:var(--footer-bottom);color:#777;font-size:10px;text-align:center;line-height:55px}
</style>
</head>
<body>

<header class="site-header">
  <div class="brand">Lantern Dwelling<br>Partners</div>
  <nav class="main-nav">
    <a class="active" style="left:542px">Home</a>
    <a style="left:610px">About Us</a>
    <a style="left:699px">Services</a>
    <a style="left:782px">Testimonials</a>
    <a style="left:893px">Contact Us</a>
  </nav>
  <div class="search-toggle">
    <svg width="14" height="14" viewBox="0 0 14 14"><circle cx="6" cy="6" r="4.2" fill="none" stroke="#fff" stroke-width="2"/><line x1="9" y1="9" x2="13" y2="13" stroke="#fff" stroke-width="2"/></svg>
  </div>
</header>

<section class="hero" role="img" aria-label="Photo of a large stone-and-shingle family house on a tree-lined street under blue sky">
  <h1 class="hero-title">SPECIALIZING IN “WARM ENVIRONMENTS”</h1>
  <div class="slider-dots"><span></span><span></span><span></span></div>
</section>

<div class="finder-shadow"></div>
<form class="finder">
  <svg class="abs" style="left:0;top:0" width="936" height="134" viewBox="0 0 936 134"><path d="M0 0H936V110Q468 150 0 110Z" fill="#8dc63f"/></svg>
  <h2>Find Your Property</h2>
  <div class="field" style="left:39px"><label>City &amp; State or Zip</label><div class="box" style="width:152px"></div></div>
  <div class="field" style="left:198px"><label>Search Area</label><div class="box select" style="width:156px">No radius</div></div>
  <div class="field" style="left:366px"><label>Price Range</label><div class="box select" style="width:99px">All Price</div></div>
  <div class="field" style="left:473px"><label>To</label><div class="box select" style="width:100px">All Price</div></div>
  <div class="field" style="left:582px"><label>Bed Room (s)</label><div class="box select" style="width:108px">Any number</div></div>
  <div class="field" style="left:699px"><label>Bath Room(s)</label><div class="box select" style="width:102px">Any number</div></div>
  <div class="search-btn">Search</div>
</form>

<h2 class="section-title intro-title">REAL ESTATES</h2>
<p class="intro-text">Condimentum in vestibulum parturient nam semper gravida ultrices class justo at ullamcorper adipiscing a a rhoncus nulla habitant risus a vestibulum feugiat enim ac. Dis id vulputate consequat non urna a lobortis egestas integer a mi a aptent a inceptos donec scelerisque dis vel iaculis. A adipiscing nisl tristique cum habitasse scelerisque diam condimentum ullamcorper semper arcu parturient parturient orci in conubia mi diam diam vestibulum.</p>
<div class="btn-teal intro-btn">READ MORE</div>

<nav class="tabs">
  <a class="active" style="left:473px">RECENT</a>
  <a style="left:556px">FEATURED</a>
  <a style="left:659px">POPULAR</a>
</nav>

<article class="listing open" style="left:140px;top:939px">
  <div class="details">
    <div class="spec">Build up : 1000 SQ FT<br>Land Size : 110 SQ FT</div>
    <p>Tincidunt parturient sodales elementum a quis vestibulum fusce a parturient scelerisque mollis cubilia purus est.</p>
    <div class="date">Added Date : 4 days ago</div>
    <div class="view">View Details</div>
  </div>
  <div class="tag">FOR RENT</div>
  <div class="address">418 HARBOR CREST AVENUE<br>LOS ANGELES, CA 90012, USA</div>
  <div class="price">$4,555/MONTH</div><div class="our">OUR PRICE : $3,555</div>
</article>

<article class="listing" style="left:455px;top:939px">
  <div class="photo" role="img" aria-label="Modern white villa with a lit swimming pool at dusk" style="background:linear-gradient(180deg,#3b5f8a,#a8b4bd 55%,#3fa7c9)"></div>
  <div class="tag">FOR SALE</div>
  <div class="address">418 HARBOR CREST AVENUE<br>LOS ANGELES, CA 90012, USA</div>
  <div class="rule"></div>
  <div class="price">$4,555/MONTH</div><div class="our">OUR PRICE : $3,555</div>
</article>

<article class="listing" style="left:771px;top:939px">
  <div class="photo" role="img" aria-label="Two-storey grey suburban house with lit windows at twilight" style="background:linear-gradient(180deg,#5b7fc0,#6c6f7a 55%,#8d8a80)"></div>
  <div class="tag">FOR SALE</div>
  <div class="address">418 HARBOR CREST AVENUE<br>LOS ANGELES, CA 90012, USA</div>
  <div class="rule"></div>
  <div class="price">$4,555/MONTH</div><div class="our">OUR PRICE : $3,555</div>
</article>

<article class="listing" style="left:140px;top:1276px">
  <div class="photo" role="img" aria-label="White modern house with palm trees and pool at sunset" style="background:linear-gradient(180deg,#3a5d99,#b98f72 55%,#4a6f8c)"></div>
  <div class="tag">FOR SALE</div>
  <div class="address">418 HARBOR CREST AVENUE<br>LOS ANGELES, CA 90012, USA</div>
  <div class="rule"></div>
  <div class="price">$4,555/MONTH</div><div class="our">OUR PRICE : $3,555</div>
</article>

<article class="listing" style="left:455px;top:1276px">
  <div class="photo" role="img" aria-label="Bright modern open-plan kitchen with pendant lamps and red chairs" style="background:linear-gradient(180deg,#e4e6e8,#b9bcbf 60%,#3a3c40)"></div>
  <div class="tag">FOR RENT</div>
  <div class="address">418 HARBOR CREST AVENUE<br>LOS ANGELES, CA 90012, USA</div>
  <div class="rule"></div>
  <div class="price">$4,555/MONTH</div><div class="our">OUR PRICE : $3,555</div>
</article>

<article class="listing" style="left:771px;top:1276px">
  <div class="photo" role="img" aria-label="Large brick family house with driveway and lawn under blue sky" style="background:linear-gradient(180deg,#3f7bd0,#a88a6f 55%,#6f8f4a)"></div>
  <div class="tag">FOR SALE</div>
  <div class="address">418 HARBOR CREST AVENUE<br>LOS ANGELES, CA 90012, USA</div>
  <div class="rule"></div>
  <div class="price">$4,555/MONTH</div><div class="our">OUR PRICE : $3,555</div>
</article>

<h2 class="section-title testi-title">TESTIMONIALS</h2>

<article class="testimonial" style="left:132px">
  <div class="head"></div><h3>AUTHOR NAME</h3>
  <div class="avatar" role="img" aria-label="Client portrait photo" style="background:linear-gradient(180deg,#b07850,#e2b89a)"></div>
  <blockquote>“ Vestibulum a imperdiet imperdiet placerat a ullamcorper a vestibulum nibh in enim himenaeos tempus metus in rhoncus.Porttitor vestibulum sapien arcu. ”</blockquote>
  <div class="btn-teal">Read more</div>
</article>
<article class="testimonial" style="left:449px">
  <div class="head"></div><h3>AUTHOR NAME</h3>
  <div class="avatar" role="img" aria-label="Client portrait photo" style="background:linear-gradient(180deg,#3a2a20,#c89a7a)"></div>
  <blockquote>“ Vestibulum a imperdiet imperdiet placerat a ullamcorper a vestibulum nibh in enim himenaeos tempus metus in rhoncus.Porttitor vestibulum sapien arcu. ”</blockquote>
  <div class="btn-teal">Read more</div>
</article>
<article class="testimonial" style="left:766px">
  <div class="head"></div><h3>AUTHOR NAME</h3>
  <div class="avatar" role="img" aria-label="Client portrait photo" style="background:linear-gradient(180deg,#6b4a35,#ecd0bc)"></div>
  <blockquote>“ Vestibulum a imperdiet imperdiet placerat a ullamcorper a vestibulum nibh in enim himenaeos tempus metus in rhoncus.Porttitor vestibulum sapien arcu. ”</blockquote>
  <div class="btn-teal">Read more</div>
</article>

<section class="join">
  <h2>JOIN US</h2>
  <div class="sub">SIGN UP FOR OUR NEWS LETTER</div>
  <div class="email">ENTER EMAIL ID
    <svg width="12" height="9" viewBox="0 0 12 9"><rect x=".5" y=".5" width="11" height="8" fill="none" stroke="#444"/><path d="M.5 .5L6 5 11.5 .5" fill="none" stroke="#444"/></svg>
  </div>
  <div class="btn-teal">SUBSCRIBE</div>
</section>

<footer class="site-footer">
  <h4 style="left:193px">QUICK LINKS</h4>
  <ul class="quick-links">
    <li>Home</li><li>About Us</li><li>Services</li><li>Testimonials</li><li>Contact Us</li>
  </ul>

  <h4 style="left:511px">CONTACT US</h4>
  <svg class="contact-icon" style="top:70px" width="11" height="15" viewBox="0 0 11 15"><path d="M5.5 14C2 9 1 7 1 5a4.5 4.5 0 0 1 9 0c0 2-1 4-4.5 9z" fill="none" stroke="#17a58a" stroke-width="1.6"/><circle cx="5.5" cy="5" r="1.6" fill="#17a58a"/></svg>
  <div class="contact-line" style="top:64px">Main Store 220 Maple Row<br>Suite 4</div>
  <svg class="contact-icon" style="top:120px" width="12" height="12" viewBox="0 0 12 12"><path d="M2 1l2.5 0 1 3-1.5 1a7 7 0 0 0 3 3l1-1.5 3 1V10c0 1-1 1.5-2 1.5C5 11 1 7 .5 3 .5 2 1 1 2 1z" fill="#17a58a"/></svg>
  <div class="contact-line" style="top:117px">(555) 014-2290</div>
  <svg class="contact-icon" style="top:150px" width="12" height="9" viewBox="0 0 12 9"><rect width="12" height="9" fill="#17a58a"/><path d="M0 0L6 5 12 0" fill="none" stroke="#000"/></svg>
  <div class="contact-line" style="top:145px">hello@lanterndwelling.example</div>

  <h4 style="left:809px">FOLLOW US</h4>
</footer>
<div class="socials"><span></span><span></span><span></span><span></span><span></span></div>
<div class="footer-brand">Lantern Dwelling<br>Partners</div>

<div class="copyright">All Rights Reserved. Copyrights @ 2016 company name</div>

</body>
</html>
```